New Business Card Design for Manufacturing

We are an engineering/manufacturing company that offers Advanced machining/assembly/engineering services, as well as innovative products for the heavy duty engine cooling markets.

We are looking to get a new business card designed that is clean and modern looking, but still fits the wide range of technical/skilled work we do.

- We hope to use this design as the base for other design work in new Presentations, web, and print work.

Industry/Entity Type

Engineering

Contact Information for Business Card

Our preferred color of blue is (RGB) 22/71/159 but can vary slightly from that color. Our content will be our Logo and full company name (Vantrell Forge Works, Inc.), company address, name, job title, phone number with extension, cell number, fax number, website, and email address on the cards.
We'd like the full company name next to the logo, but we are open to other interpretations of that layout.
Preferably, we would like the back side to be clean with just our logo, and the front to contain all of the contact information.

Colors
2f74b4
0355a3
85abd2

Requirements
Must have
• - Logo, company name, needed content - We are open to interpretation beyond that.
• - Standard size business card.
• - Horizontal orientation.
• - Enough space for lengthy names / job titles (for example, a job title could read "Directory of Human Resources" or "V.P. of Governmental Affairs"). We need this to look clean, whether the title be short (CEO) or long (as described above).

```html
<!DOCTYPE html>
<html lang="en">
<head>
<meta charset="utf-8">
<title>Vantrell Forge Works – Business Card</title>
<link rel="stylesheet" href="https://fonts.googleapis.com/css2?family=Fira+Sans:wght@400;500;700;800&display=swap">
<style>
  :root {
    --brand-blue: #0355a3;
    --brand-blue-deep: #02498d;
    --accent-gray: #7d8791;
    --paper: #ffffff;
    --backdrop: #e4e4e4;
    --ink-muted: #3b3f44;
  }
  * { margin: 0; padding: 0; box-sizing: border-box; }
  html, body { width: 1200px; height: 576px; overflow: hidden; }
  body {
    background: var(--backdrop);
    font-family: "Fira Sans", Arial, sans-serif;
    position: relative;
  }
  .card {
    position: absolute;
    top: 138px;
    width: 484px;
    height: 294px;
    border-radius: 16px;
    overflow: hidden;
    box-shadow: 0 3px 6px rgba(0,0,0,0.22);
  }

  /* Back side */
  .card-back {
    left: 82px;
    background: linear-gradient(180deg, var(--brand-blue) 0%, var(--brand-blue-deep) 100%);
    color: var(--paper);
  }
  .card-back .brand-block {
    position: absolute;
    left: 0; right: 0;
    top: 100px;
    text-align: center;
  }
  .card-back .wordmark {
    font-weight: 800;
    font-size: 40px;
    line-height: 1;
    letter-spacing: 1px;
    text-transform: uppercase;
  }
  .card-back .tagline {
    margin-top: 14px;
    font-weight: 700;
    font-size: 17px;
    letter-spacing: 1px;
  }
  .card-back .web-line {
    position: absolute;
    left: 0; right: 0;
    top: 264px;
    display: flex;
    justify-content: center;
    align-items: center;
    gap: 12px;
    font-size: 13px;
  }
  .card-back .rule {
    width: 52px; height: 2px;
    background: var(--paper);
    border-radius: 1px;
  }

  /* Front side */
  .card-front {
    left: 602px;
    width: 481px;
    background: var(--paper);
  }
  .card-front .edge-dot {
    position: absolute;
    left: -18px; top: 24px;
    width: 36px; height: 36px;
    border-radius: 50%;
    background: var(--brand-blue);
  }
  .card-front .person {
    position: absolute;
    left: 22px; top: 26px;
    max-width: 200px;
  }
  .card-front .person-name {
    font-size: 20px;
    font-weight: 500;
    line-height: 1.15;
    color: var(--brand-blue);
  }
  .card-front .person-title {
    margin-top: 4px;
    font-size: 12px;
    line-height: 1.3;
    color: var(--ink-muted);
  }
  .card-front .brand-block {
    position: absolute;
    right: 26px; top: 40px;
    text-align: center;
  }
  .card-front .wordmark {
    font-weight: 800;
    font-size: 28px;
    line-height: 1;
    color: var(--brand-blue);
    text-transform: uppercase;
    white-space: nowrap;
  }
  .card-front .tagline {
    margin-top: 8px;
    font-weight: 700;
    font-size: 12px;
    letter-spacing: 0.8px;
    color: var(--accent-gray);
  }
  .card-front .company-name {
    position: absolute;
    right: 22px; top: 126px;
    font-size: 14.5px;
    font-weight: 500;
    color: var(--brand-blue);
  }
  .card-front .wave { position: absolute; left: 0; top: 0; }
  .contact-list {
    position: absolute;
    left: 22px; top: 190px;
    list-style: none;
    color: var(--paper);
    font-size: 12.5px;
  }
  .contact-list li {
    display: flex;
    align-items: center;
    height: 17.4px;
    gap: 9px;
  }
  .contact-list svg { width: 11px; height: 11px; fill: var(--paper); flex: none; }
  .address {
    position: absolute;
    right: 22px; top: 242px;
    text-align: right;
    color: var(--paper);
    font-size: 12.5px;
    line-height: 17.4px;
    font-style: normal;
  }
</style>
</head>
<body>

  <section class="card card-back" aria-label="Card back">
    <div class="brand-block">
      <div class="wordmark">Vantrell Forge</div>
      <div class="tagline">BUILT TO ENDURE</div>
    </div>
    <div class="web-line"><span class="rule"></span><span>www.vantrellforge.com</span><span class="rule"></span></div>
  </section>

  <section class="card card-front" aria-label="Card front">
    <svg class="wave" width="481" height="294" viewBox="0 0 481 294" aria-hidden="true">
      <path fill="var(--accent-gray)" d="M0,118 C90,96 180,122 270,162 C350,196 430,194 481,166 L481,180 C430,208 350,210 266,176 C180,140 90,114 0,130 Z"/>
      <path fill="var(--brand-blue)" d="M0,136 C90,120 175,142 262,182 C342,214 425,214 481,188 L481,294 L0,294 Z"/>
    </svg>
    <span class="edge-dot"></span>
    <div class="person">
      <div class="person-name">Dana Marlowe Reyes</div>
      <div class="person-title">Managing Director</div>
    </div>
    <div class="brand-block">
      <div class="wordmark">Vantrell Forge</div>
      <div class="tagline">BUILT TO ENDURE</div>
    </div>
    <div class="company-name">Vantrell Forge Works, Inc.</div>

    <ul class="contact-list">
      <li><svg viewBox="0 0 12 12"><path d="M1 3c0-1 1-2 5-2s5 1 5 2v1H8V3H4v1H1zM2 5h8l1 6H1z"/></svg>555-0142-7700 (VFW)</li>
      <li><svg viewBox="0 0 12 12"><path d="M3 0h6v12H3zM4 1.5v8h4v-8z"/></svg>555-0188-3261</li>
      <li><svg viewBox="0 0 12 12"><path d="M3 0h6v3H3zM0 4h12v5H0zM3 7h6v5H3z"/></svg>555-0142-7799</li>
      <li><svg viewBox="0 0 12 12"><path d="M0 2h12v1L6 7 0 3zM0 4.5l6 4 6-4V10H0z"/></svg>dreyes@vantrellforge.com</li>
      <li><svg viewBox="0 0 12 12"><path d="M6 0a6 6 0 1 0 0 12A6 6 0 0 0 6 0zm0 1.2c.8.9 1.3 2.2 1.4 3.8H4.6C4.7 3.4 5.2 2.1 6 1.2zM4.6 7h2.8c-.1 1.6-.6 2.9-1.4 3.8-.8-.9-1.3-2.2-1.4-3.8z"/></svg>www.vantrellforge.com</li>
    </ul>

    <address class="address">418 Millrace Ave., Suite 2<br>Harlow Falls, OH 45871</address>
  </section>

</body>
</html>
```